Communication and Marketing agency needs a new presentation card

We are a group of communication and marketing agencies specialized in companies that are in the logistics and industrial sector. The head agency is TELVANO Grupo and the group consists of 4 agencies: TELVANO Media, TELVANO Digital, TELVANO Research and DifundeEnPantalla. We hace 4 offices in Spain (Madrid, Barcelona, Valencia and Murcia). We are looking for a clean and attractive design that transmits our experience, brand presence in the market and knowledge to those who receive the card.It has to maintain the colors of the logo that is attached.
Target Market(s)
logistics and industrial sector
Marketing department
Contact Information for Business Card
Clean and attractive design

```html
<!DOCTYPE html>
<html lang="es">
<head>
<meta charset="utf-8">
<title>TELVANO Grupo – Tarjeta de presentación</title>
<link href="https://fonts.googleapis.com/css2?family=Oswald:wght@400;500&family=PT+Sans:wght@400;700&display=swap" rel="stylesheet">
<style>
  :root {
    --bg: #e9e7e6;
    --card: #fbfbfb;
    --red: #b0222a;
    --grey: #58595b;
    --ink: #2b2b2b;
    --text: #333333;
  }
  * { margin: 0; padding: 0; box-sizing: border-box; }
  html, body { width: 1200px; height: 1200px; overflow: hidden; }
  body {
    background: var(--bg);
    position: relative;
    font-family: "PT Sans", sans-serif;
    color: var(--text);
  }
  .card {
    position: absolute;
    left: 224px;
    width: 814px;
    background: var(--card);
  }
  .card--front { top: 76px; height: 465px; border-radius: 26px; }
  .card--back { top: 658px; height: 464px; }

  .wordmark {
    position: absolute;
    text-align: right;
    font-family: "Oswald", sans-serif;
    font-weight: 500;
    line-height: 1;
  }
  .wordmark__main { display: block; font-size: 96px; letter-spacing: 6px; margin-right: -6px; }
  .wordmark__sub { display: block; font-size: 54px; margin-top: 4px; }

  .card--front .wordmark { right: 152px; top: 148px; color: var(--grey); }
  .card--back .wordmark { right: 86px; top: 40px; color: var(--red); }

  .holder {
    position: absolute;
    left: 67px;
    top: 252px;
  }
  .holder__name {
    font-family: "Oswald", sans-serif;
    font-weight: 500;
    font-size: 38px;
    line-height: 1.1;
    color: var(--ink);
    text-transform: uppercase;
    letter-spacing: -0.5px;
  }
  .holder__first { color: var(--red); }
  .holder__role {
    margin-top: 10px;
    font-size: 17px;
    letter-spacing: 0.5px;
    color: var(--text);
  }

  .rule {
    display: block;
    width: 51px;
    height: 3px;
    background: var(--red);
  }

  .contact {
    position: absolute;
    top: 336px;
    font-size: 17px;
    line-height: 23.5px;
  }
  .contact .rule { margin-bottom: 20px; }
  .contact--person { left: 67px; }
  .contact--office { left: 553px; }
  .contact__label { color: var(--red); font-weight: 700; }
  .contact__accent { color: var(--red); }
</style>
</head>
<body>

  <section class="card card--front" aria-label="Anverso">
    <div class="wordmark">
      <span class="wordmark__main">TELVANO</span>
      <span class="wordmark__sub">Digital</span>
    </div>
  </section>

  <section class="card card--back" aria-label="Reverso">
    <div class="wordmark">
      <span class="wordmark__main">TELVANO</span>
      <span class="wordmark__sub">Grupo</span>
    </div>

    <div class="holder">
      <h1 class="holder__name"><span class="holder__first">Lucas</span> Moreno</h1>
      <p class="holder__role">MANAGER</p>
    </div>

    <div class="contact contact--person">
      <span class="rule"></span>
      <p><span class="contact__label">P.</span> +(915) -482- 3176</p>
      <p><span class="contact__label">F.</span> +(915) -482- 3176</p>
      <p>contacto@lineaventas.com</p>
    </div>

    <div class="contact contact--office">
      <span class="rule"></span>
      <p>Calle de Alcalá 214,</p>
      <p>28028 Madrid, España</p>
      <p>www.<span class="contact__accent">telvanogrupo</span>.com</p>
    </div>
  </section>

</body>
</html>
```